Business card design for new eCommerce site focusing on integrity and strong businsess tactics

We need a business card that will stand out and be memorable. Something with color that matches our company logo colors. Think high end version of Pactivo. There are 2 logos provided. The parent company is called Amber Ledge Partners and we are presenting a new and very exciting eCommerce site called BrightHarborTrade.example.

Target Market(s)

Our target markets are in the Activities, Food and Beverage, Health and Beauty

Industry/Entity Type

Marketing

Contact Information for Business Card

We have 4 members that need cards...I will provide all info to the winner of the design contest
Business Address is
4870 West 63rd Avenue, Suite C207
Phoenix AZ 85731

Font styles to use
Serif
Sans Serif

Colors

Designer to choose colors to be used in the design.

Requirements
Must have
• The card must be memorable...should be unique in design but must exude integrity and be playful .
• I have provided several colors or our parent company...please feel free to use which ever
Nice to have
• I will leave this up to you. Feel free to use other images of your choosing that wraps around our client.....Activities, Dining, Health, Beauty
Should not have
• just dont be boring

```html
<!DOCTYPE html>
<html lang="en">
<head>
<meta charset="utf-8">
<title>Amber Ledge Partners – Business Card</title>
<link rel="stylesheet" href="https://fonts.googleapis.com/css2?family=Montserrat:wght@400;500;700&family=Poppins:wght@300;400;500&display=swap">
<style>
  :root {
    --stage: #1c1d1f;
    --card-white: #ffffff;
    --teal: #2a9d93;
    --ink: #4a4a4a;
    --ink-soft: #6b6b6b;
    --blue-dark: #23689b;
    --blue: #2f80b9;
    --blue-light: #3a8cc4;
    --on-blue: #f2f5f7;
  }
  * { box-sizing: border-box; margin: 0; padding: 0; }
  html, body { width: 1200px; height: 963px; overflow: hidden; }
  body {
    background: var(--stage);
    font-family: "Poppins", sans-serif;
    display: flex;
    flex-direction: column;
    align-items: center;
    justify-content: center;
    gap: 48px;
  }
  .card {
    width: 700px;
    height: 400px;
    border-radius: 22px;
    position: relative;
    overflow: hidden;
    box-shadow: 0 18px 40px rgba(0,0,0,.45);
  }

  /* Front */
  .card-front { background: var(--card-white); }
  .brand-block {
    position: absolute;
    left: 60px; top: 140px;
    width: 280px;
    display: flex; flex-direction: column; align-items: center; gap: 14px;
  }
  .brand-dot {
    width: 46px; height: 46px; border-radius: 50%;
    background: var(--teal);
  }
  .brand-name {
    font-family: "Montserrat", sans-serif;
    font-weight: 700;
    font-size: 28px;
    color: var(--teal);
    text-align: center;
    line-height: 1.1;
  }
  .divider {
    position: absolute;
    left: 370px; top: 120px;
    width: 2px; height: 150px;
    background: var(--teal);
  }
  .person {
    position: absolute;
    left: 400px; top: 125px;
  }
  .person-name {
    font-family: "Montserrat", sans-serif;
    font-weight: 700; font-size: 22px; color: var(--teal);
  }
  .person-role { font-size: 17px; color: var(--ink-soft); margin-top: 2px; }
  .contacts { list-style: none; margin-top: 16px; display: flex; flex-direction: column; gap: 6px; }
  .contacts li { display: flex; align-items: center; gap: 10px; font-size: 14px; color: var(--ink); }
  .contacts svg { width: 13px; height: 13px; flex: none; }
  .address {
    position: absolute;
    left: 60px; bottom: 48px;
    font-size: 15px; color: var(--ink);
    letter-spacing: .2px;
  }

  /* Back */
  .card-back {
    background: radial-gradient(ellipse at 70% 45%, var(--blue-light) 0%, var(--blue) 45%, var(--blue-dark) 100%);
    color: var(--on-blue);
  }
  .back-brand {
    position: absolute; left: 70px; top: 120px;
    display: flex; align-items: center; gap: 20px;
  }
  .back-dot { width: 58px; height: 58px; border-radius: 50%; background: var(--on-blue); }
  .back-name {
    font-family: "Poppins", sans-serif; font-weight: 500; font-size: 36px; line-height: 1;
  }
  .tagline { font-size: 17px; letter-spacing: 1.5px; margin-top: 8px; font-weight: 300; }
  .back-url {
    position: absolute; left: 148px; top: 265px;
    font-size: 15px; letter-spacing: 2.5px; font-weight: 300;
  }
</style>
</head>
<body>
  <section class="card card-front" aria-label="Card front">
    <div class="brand-block">
      <span class="brand-dot"></span>
      <span class="brand-name">Amber Ledge Partners</span>
    </div>
    <span class="divider"></span>
    <div class="person">
      <p class="person-name">Dana Whitlock</p>
      <p class="person-role">Founder</p>
      <ul class="contacts">
        <li>
          <svg viewBox="0 0 12 12"><rect x="2.5" y="0.5" width="7" height="11" rx="1.2" fill="none" stroke="var(--teal)" stroke-width="1.2"/></svg>
          0400 555 019
        </li>
        <li>
          <svg viewBox="0 0 12 12"><rect x="0.5" y="2" width="11" height="8" fill="var(--teal)"/><path d="M0.5 2 L6 6.5 L11.5 2" fill="none" stroke="#fff" stroke-width="1"/></svg>
          info@brightharbortrade.example
        </li>
        <li>
          <svg viewBox="0 0 12 12"><circle cx="5" cy="5" r="3.6" fill="none" stroke="var(--teal)" stroke-width="1.5"/><line x1="7.6" y1="7.6" x2="11" y2="11" stroke="var(--teal)" stroke-width="1.6"/></svg>
          www.brightharbortrade.example
        </li>
      </ul>
    </div>
    <p class="address">4870 West 63rd Avenue, Suite C207 Phoenix AZ 85731</p>
  </section>

  <section class="card card-back" aria-label="Card back">
    <div class="back-brand">
      <span class="back-dot"></span>
      <div>
        <p class="back-name">BrightHarborTrade.example</p>
        <p class="tagline">Activities-Dining-Health-Beauty</p>
      </div>
    </div>
    <p class="back-url">www.amberledgepartners.example</p>
  </section>
</body>
</html>
```